Tavel Website

Need a 4 page Drupal website - Home, About Us, Portfolio, Contact for a private equity/venture capital firm and new logo - company name is Tavel Corporation. The design should communicate - stock markets, hedge funds, deal-making, investments. The Portfolio section is to showcase the small companies we invest in. Hoping for something fresh, dynamic, even fun - no cliche financial images of New York. Not technical - but know how use Drupal content management to make text edits, blocks, articles, etc. We don't use any social media - so no chirply, Pagebook or WorkNode links. We need space for a post heron email sign-up form. Need website uploaded to my Corvane web hosting account. First time user of Sketch Plaza - have 3 other company websites that need refreshing.

```html
<!DOCTYPE html>
<html lang="en">
<head>
<meta charset="utf-8">
<title>Tavel Corporation</title>
<link rel="stylesheet" href="https://fonts.googleapis.com/css2?family=Roboto:wght@400;500;700&family=Montserrat:wght@700&display=swap">
<style>
:root{
  --teal:#1fb89e;
  --teal-dark:#179c86;
  --yellow:#ffd200;
  --ink:#3a3b45;
  --text:#5b5d63;
  --muted:#77797e;
  --ring:#e3e3e3;
  --band:#f5f5f5;
  --footer:#2a2b2e;
  --white:#ffffff;
}
*{margin:0;padding:0;box-sizing:border-box}
html,body{width:821px;height:1200px;overflow:hidden}
body{position:relative;background:var(--white);font-family:'Roboto',Arial,sans-serif;color:var(--text)}
.abs{position:absolute}

/* header */
.site-header{left:0;top:0;width:821px;height:55px;background:var(--teal)}
.brand{display:flex;align-items:center;gap:7px;font-family:'Montserrat',Arial,sans-serif;font-weight:700;font-size:17px;color:var(--white);letter-spacing:.2px}
.brand-mark{width:10px;height:10px;background:var(--yellow)}
.site-header .brand{left:89px;top:16px}
.main-nav a{position:absolute;top:20px;font-size:11px;color:var(--white);text-decoration:none}
.main-nav a.active{color:var(--yellow)}
.search{left:616px;top:16px;width:115px;height:22px;background:var(--white);border-radius:2px;font-size:9px;color:var(--ink);padding:6px 7px}
.search svg{position:absolute;right:6px;top:5px}

/* hero */
.hero{left:0;top:55px;width:821px;height:256px;background:linear-gradient(100deg,#e6e9ec 0%,#f6f6f6 35%,#d9c1ae 55%,#c69a80 70%,#eceae8 90%)}
.slide-arrow{top:164px}

/* welcome */
.welcome{left:0;top:311px;width:821px;height:142px;background:var(--band);text-align:center}
.welcome h1{margin-top:13px;font-size:24px;font-weight:700;color:var(--ink)}
.welcome p{width:640px;margin:10px auto 0;font-size:10.5px;line-height:17px;color:var(--text)}
.btn-yellow{display:inline-block;background:var(--yellow);color:var(--ink);font-size:12px;font-weight:500}
.welcome .btn-yellow{margin-top:12px;width:96px;height:29px;line-height:29px}

/* services */
.service{top:476px;width:180px;text-align:center}
.service h2{font-size:15px;font-weight:700;color:var(--ink)}
.service svg{display:block;margin:12px auto 0}
.service p{margin-top:12px;font-size:9.6px;line-height:17px;color:var(--muted);padding:0 8px}
.btn-dark{display:inline-block;margin-top:9px;width:73px;height:33px;line-height:33px;background:var(--ink);color:var(--white);font-size:12px}

/* portfolio */
.portfolio-head{left:0;top:754px;width:821px;text-align:center}
.portfolio-head h2{font-size:24px;font-weight:700;color:var(--ink)}
.portfolio-head p{width:640px;margin:8px auto 0;font-size:10.5px;line-height:17px;color:var(--text)}
.partner{top:840px;width:97px;text-align:center}
.partner-box{height:76px;border:1px solid #d8d8d8;display:flex;align-items:center;justify-content:center;font-size:13px;font-weight:500;color:var(--ink)}
.partner-name{margin-top:10px;font-size:10.5px;color:var(--text)}
.carousel-arrow{top:860px}

/* newsletter */
.newsletter{left:0;top:969px;width:821px;height:172px;background:linear-gradient(120deg,#3aa891 0%,#51b9a3 45%,#3ea58f 100%);text-align:center;color:var(--white)}
.newsletter h2{margin-top:20px;font-size:22px;font-weight:700}
.newsletter h2 span{color:var(--yellow)}
.newsletter p{width:650px;margin:8px auto 0;font-size:10.5px;line-height:17px}
.field{top:110px;height:36px;background:var(--white);font-size:10.5px;color:var(--text);padding:11px 9px;text-align:left}
.newsletter .btn-yellow{position:absolute;left:592px;top:110px;width:139px;height:36px;line-height:36px;font-size:15px}

/* footer */
.site-footer{left:0;top:1141px;width:821px;height:59px;background:var(--footer)}
.site-footer .brand{left:89px;top:20px}
.copyright{right:90px;top:23px;font-size:10.5px;color:var(--white)}
</style>
</head>
<body>

<header class="site-header abs">
  <div class="brand abs"><span class="brand-mark"></span>TAVEL CORPORATION</div>
  <nav class="main-nav">
    <a class="active" href="#" style="left:329px">Home</a>
    <a href="#" style="left:393px">About Us</a>
    <a href="#" style="left:474px">Portfolio</a>
    <a href="#" style="left:551px">Contact</a>
  </nav>
  <div class="search abs">Search
    <svg width="12" height="12" viewBox="0 0 12 12"><circle cx="5" cy="5" r="3.6" fill="none" stroke="var(--teal)" stroke-width="1.8"/><line x1="7.6" y1="7.6" x2="11" y2="11" stroke="var(--teal)" stroke-width="2"/></svg>
  </div>
</header>

<section class="hero abs" role="img" aria-label="Photo of a hand placing a gold coin onto a stack of coins">
  <svg class="slide-arrow abs" style="left:8px" width="24" height="24" viewBox="0 0 24 24"><circle cx="12" cy="12" r="11" fill="#fff" fill-opacity=".5" stroke="#888" stroke-width="1.2"/><path d="M14 7 L8 12 L14 17 Z" fill="#888"/></svg>
  <svg class="slide-arrow abs" style="left:789px" width="24" height="24" viewBox="0 0 24 24"><circle cx="12" cy="12" r="11" fill="#fff" fill-opacity=".5" stroke="#888" stroke-width="1.2"/><path d="M10 7 L16 12 L10 17 Z" fill="#888"/></svg>
</section>

<section class="welcome abs">
  <h1>Welcome to Tavel Corporation</h1>
  <p>Lorem ipsum dolor sit amet, duis sanctus volutpat ad vix. Omnium adipisci instructior ex ius. Mel summo scripserit at.&nbsp; Eum doctus iisque no, ut laudem elaboraret efficiendi eos. Ad per saperet intellegebat, per solum quando ad, no purto aliquando vim.</p>
  <span class="btn-yellow">Read More</span>
</section>

<!-- services -->
<article class="service abs" style="left:59px">
  <h2>Stock markets</h2>
  <svg width="112" height="112" viewBox="0 0 112 112">
    <circle cx="56" cy="56" r="51" fill="none" stroke="var(--ring)" stroke-width="6"/>
    <circle cx="56" cy="56" r="51" fill="none" stroke="var(--teal)" stroke-width="6" stroke-dasharray="160 400" transform="rotate(90 56 56)"/>
    <text x="38" y="56" font-family="Roboto,sans-serif" font-weight="700" font-size="20" fill="var(--ink)">$</text>
    <g fill="none" stroke="var(--ink)" stroke-width="2">
      <rect x="41" y="63" width="6" height="12"/><rect x="50" y="56" width="6" height="19"/><rect x="59" y="50" width="6" height="25"/>
      <path d="M62 48 V36 M56 42 L62 34 L68 42 M68 42 V74"/>
      <line x1="37" y1="78" x2="73" y2="78"/>
    </g>
  </svg>
  <p>Mei rebum ubique id. Nobis civibus his ea, no duo everti referrentur.</p>
  <span class="btn-dark">More</span>
</article>

<article class="service abs" style="left:237px">
  <h2>Hedge funds</h2>
  <svg width="112" height="112" viewBox="0 0 112 112">
    <circle cx="56" cy="56" r="51" fill="none" stroke="var(--ring)" stroke-width="6"/>
    <circle cx="56" cy="56" r="51" fill="none" stroke="var(--ink)" stroke-width="6" stroke-dasharray="210 400" transform="rotate(35 56 56)"/>
    <g fill="var(--ink)">
      <circle cx="48" cy="33" r="5"/>
      <rect x="41" y="40" width="14" height="36" rx="2"/>
      <path d="M58 56 Q56 50 62 48 L68 48 Q74 50 72 56 Q80 62 78 72 Q76 78 65 78 Q54 78 52 72 Q50 62 58 56 Z"/>
    </g>
    <text x="60" y="74" font-family="Roboto,sans-serif" font-weight="700" font-size="12" fill="#fff">$</text>
  </svg>
  <p>Mei rebum ubique id. Nobis civibus his ea, no duo everti referrentur.</p>
  <span class="btn-dark">More</span>
</article>

<article class="service abs" style="left:409px">
  <h2>Deal-making</h2>
  <svg width="112" height="112" viewBox="0 0 112 112">
    <circle cx="56" cy="56" r="51" fill="none" stroke="var(--ring)" stroke-width="6"/>
    <circle cx="56" cy="56" r="51" fill="none" stroke="var(--teal)" stroke-width="6" stroke-dasharray="150 400" transform="rotate(185 56 56)"/>
    <g fill="none" stroke="var(--ink)" stroke-width="2.5">
      <rect x="32" y="35" width="34" height="24"/>
      <line x1="40" y1="64" x2="58" y2="64"/>
    </g>
    <circle cx="44" cy="46" r="6" fill="none" stroke="var(--ink)" stroke-width="2"/>
    <circle cx="64" cy="52" r="7" fill="var(--ink)"/>
    <path d="M52 78 Q52 62 64 62 Q76 62 76 78 Z" fill="var(--ink)"/>
  </svg>
  <p>Mei rebum ubique id. Nobis civibus his ea, no duo everti referrentur.</p>
  <span class="btn-dark">More</span>
</article>

<article class="service abs" style="left:581px">
  <h2>Investments</h2>
  <svg width="112" height="112" viewBox="0 0 112 112">
    <circle cx="56" cy="56" r="51" fill="none" stroke="var(--ring)" stroke-width="6"/>
    <circle cx="56" cy="56" r="51" fill="none" stroke="var(--ink)" stroke-width="6" stroke-dasharray="185 400" transform="rotate(-90 56 56)"/>
    <g transform="rotate(25 56 56)">
      <rect x="34" y="42" width="44" height="26" rx="3" fill="var(--ink)"/>
      <circle cx="56" cy="55" r="8" fill="#fff"/>
      <text x="52" y="60" font-family="Roboto,sans-serif" font-weight="700" font-size="13" fill="var(--ink)">$</text>
    </g>
  </svg>
  <p>Mei rebum ubique id. Nobis civibus his ea, no duo everti referrentur.</p>
  <span class="btn-dark">More</span>
</article>

<section class="portfolio-head abs">
  <h2>Portfolio</h2>
  <p>Pro animal nominati volutpat ut, epicuri expetendis an mel. Nam salutandi constituto disputando ut, eos tale labitur ex, nam civibus repudiare rimique eu. Mea dico repudiandae comprehensam at.</p>
</section>

<svg class="carousel-arrow abs" style="left:90px" width="16" height="32" viewBox="0 0 16 32"><path d="M14 2 L2 16 L14 30" fill="none" stroke="#c4c4c4" stroke-width="2"/></svg>
<svg class="carousel-arrow abs" style="left:715px" width="16" height="32" viewBox="0 0 16 32"><path d="M2 2 L14 16 L2 30" fill="none" stroke="#c4c4c4" stroke-width="2"/></svg>

<div class="partner abs" style="left:130px"><div class="partner-box">Norvela</div><div class="partner-name">Norvela D/B/A</div></div>
<div class="partner abs" style="left:245px"><div class="partner-box">Brisk Step</div><div class="partner-name">Brisk Step Inc</div></div>
<div class="partner abs" style="left:361px"><div class="partner-box">Lumora</div><div class="partner-name">Lumora Bio Inc</div></div>
<div class="partner abs" style="left:476px"><div class="partner-box">Kestrel</div><div class="partner-name" style="margin-left:-6px;margin-right:-6px">Kestrel Industries Inc</div></div>
<div class="partner abs" style="left:591px"><div class="partner-box">Halden</div><div class="partner-name">Halden Inc</div></div>

<section class="newsletter abs">
  <h2>Newsletter <span>Signup</span></h2>
  <p>Aliquam inciderint eu vel. At est lorem tantas electram, docendi inimicus iracundia an sit. Ex mel exerci tincidunt, sit in senserit reformida-Dicta soluta phaedrum ad vim. Pro ea sint aliquam verterem, ne nullam offendit platonem cum.</p>
  <div class="field abs" style="left:90px;width:238px">Enter Your Name</div>
  <div class="field abs" style="left:340px;width:238px">Enter Your Email</div>
  <span class="btn-yellow">Subscribe</span>
</section>

<footer class="site-footer abs">
  <div class="brand abs"><span class="brand-mark"></span>TAVEL CORPORATION</div>
  <div class="copyright abs">Copyright @ 2014 Tavel Corporation.All Rights Reserved.</div>
</footer>

</body>
</html>
```